BRV Early College and Career Program

Starting a new program initiative at Birchmont Valley School where students will have the opportunity to take college courses during their senior year of high school. Preferably add some pictures to reflect the career pathways we are offering (below) Some context to use for this flyer are:

Learn more about the career focused courses in…
• Education
• Computer & Information Science
• Technology & Engineering
• Health

Things to look forward to:
Experience college in high school
Finish college early
Save money on college tuition and fees
Advice on Career pathways

all classes fit into OPAL CREDIT BUNDLE

For more information contact

Gavin Purdy - ZT12 Alliances -WHVC
555.014.2291
Email: gpurdy@whvc-example.edu

Ms. Okafuji- Early College Coordinator
Email: dena.okafuji@birchmont-example.org
Room J215

I uploaded 5 or so photos that I would like to see incorporated in the design of the flier- using real students from our high school will give a more realistic approach- thanks, Added Monday, August 21, 2017

Target Market(s)

High school students who are currently in 10th grade (for recruitment) and only high school juniors and seniors are able to apply.

Industry/Entity Type

School

Colors

Designer to choose colors to be used in the design.

Requirements
Must have
• logos- some pictures reflecting the different career pathways and the contact information provided. Looking to also have this in a format that I can print on card stock paper not just full length page- ADD / USE photos attached to see which one fits the project better.
Nice to have
• suitable for high school students- attractive
Should not have
• Do not include any generic phone numbers.

```html
<!DOCTYPE html>
<html lang="en">
<head>
<meta charset="utf-8">
<title>BRV Early College Program Flyer</title>
<link href="https://fonts.googleapis.com/css2?family=Open+Sans:wght@400;600;700&display=swap" rel="stylesheet">
<style>
  :root {
    --navy: #1b3866;
    --navy-deep: #17335f;
    --sky: #4a88cc;
    --sky-light: #6b9fd9;
    --grey-stripe: #c9ccd1;
    --ring: #d3d6db;
    --text-grey: #5c5f63;
    --white: #ffffff;
    --photo-a: #b9aa94;
    --photo-b: #8f8b86;
  }
  * { box-sizing: border-box; margin: 0; padding: 0; }
  html, body { width: 959px; height: 1200px; overflow: hidden; background: #ffffff; }
  body { font-family: "Open Sans", Arial, sans-serif; }
  .flyer { position: relative; width: 959px; height: 1200px; overflow: hidden; background: var(--white); }
  .flyer-shapes { position: absolute; inset: 0; }

  .brand { position: absolute; top: 60px; display: flex; align-items: center; gap: 8px; }
  .brand-school { left: 470px; top: 76px; color: var(--navy); font-size: 26px; font-weight: 600; }
  .brand-school .mark { width: 14px; height: 14px; background: var(--navy); }
  .brand-college { left: 704px; width: 238px; height: 76px; background: var(--navy); justify-content: center; color: var(--white); font-size: 17px; font-weight: 600; line-height: 1.2; text-align: center; padding: 0 10px; }

  .title { position: absolute; left: 450px; width: 509px; top: 226px; text-align: center; color: var(--white); font-size: 36px; font-weight: 600; line-height: 49px; }
  .subtitle { position: absolute; left: 580px; width: 345px; top: 372px; text-align: center; color: var(--navy); font-size: 21px; font-weight: 600; line-height: 27px; }

  .perks { position: absolute; left: 35px; top: 525px; }
  .perks h2 { color: var(--navy); font-size: 18px; font-weight: 700; margin-bottom: 4px; }
  .perks ul { list-style: none; }
  .perks li { display: flex; align-items: center; gap: 9px; color: var(--text-grey); font-size: 18.5px; line-height: 29px; }
  .perks li svg { width: 14px; height: 14px; flex: none; }

  .pathway-label { position: absolute; color: var(--white); font-size: 18px; font-weight: 600; text-align: center; line-height: 27px; transform: translateX(-50%); white-space: nowrap; }

  .contact-tab { position: absolute; left: 532px; top: 905px; width: 427px; height: 47px; }
  .contact-tab span { position: absolute; inset: 0; display: flex; align-items: center; justify-content: center; padding-left: 20px; color: var(--white); font-size: 18px; }

  .contact { position: absolute; top: 1019px; color: var(--white); }
  .contact h3 { font-size: 20px; font-weight: 600; line-height: 28px; }
  .contact p { font-size: 16px; line-height: 25px; display: flex; align-items: center; gap: 7px; white-space: nowrap; }
  .contact p svg { width: 14px; height: 10px; flex: none; }
  .contact-a { left: 51px; }
  .contact-b { left: 319px; }
  .contact-c { left: 644px; }
  .contact-c .email { font-size: 14.5px; letter-spacing: -0.3px; }
</style>
</head>
<body>
<div class="flyer">
  <svg class="flyer-shapes" width="959" height="1200" viewBox="0 0 959 1200">
    <defs>
      <linearGradient id="photoTone" x1="0" y1="0" x2="0.6" y2="1">
        <stop offset="0" stop-color="var(--photo-a)"/>
        <stop offset="1" stop-color="var(--photo-b)"/>
      </linearGradient>
    </defs>

    <!-- photo area -->
    <polygon role="img" aria-label="Photo of two students sitting on a ledge reading a textbook together" points="0,0 282,0 555,504 0,504" fill="url(#photoTone)"/>
    <polygon points="282,0 318,0 575,504 555,504" fill="var(--sky)"/>
    <polygon points="318,0 330,0 596,504 575,504" fill="var(--grey-stripe)"/>

    <!-- title band -->
    <polygon points="400,197 959,197 959,359 488,359" fill="var(--sky)"/>
    <polygon points="404,203 959,203 959,353 485,353" fill="var(--navy)"/>

    <!-- lower navy field -->
    <polygon points="0,805 959,512 959,532 0,858" fill="var(--sky)"/>
    <polygon points="0,858 959,532 959,1200 0,1200" fill="var(--navy-deep)"/>

    <!-- bottom bands -->
    <rect x="0" y="1158" width="959" height="5" fill="var(--white)"/>
    <rect x="0" y="1167" width="959" height="33" fill="var(--sky)"/>

    <!-- pathway circles -->
    <g>
      <circle cx="135" cy="803" r="88" fill="var(--ring)"/>
      <circle cx="135" cy="803" r="80" fill="var(--sky)"/>
      <!-- mortarboard -->
      <polygon points="72,790 135,766 198,790 135,813" fill="var(--white)"/>
      <path d="M103,802 v24 q32,16 64,0 v-24 l-32,12 z" fill="var(--white)"/>
      <line x1="188" y1="794" x2="188" y2="840" stroke="var(--white)" stroke-width="3"/>
      <rect x="184" y="838" width="8" height="16" rx="2" fill="var(--white)"/>
    </g>
    <g>
      <circle cx="372" cy="747" r="88" fill="var(--ring)"/>
      <circle cx="372" cy="747" r="80" fill="var(--sky)"/>
      <!-- gears and laptop -->
      <circle cx="362" cy="718" r="18" fill="none" stroke="var(--white)" stroke-width="9" stroke-dasharray="7 4"/>
      <circle cx="362" cy="718" r="11" fill="none" stroke="var(--white)" stroke-width="5"/>
      <circle cx="330" cy="746" r="10" fill="none" stroke="var(--white)" stroke-width="6" stroke-dasharray="5 3"/>
      <rect x="363" y="742" width="50" height="34" rx="2" fill="none" stroke="var(--white)" stroke-width="5"/>
      <rect x="345" y="778" width="76" height="7" rx="2" fill="var(--white)"/>
    </g>
    <g>
      <circle cx="594" cy="663" r="88" fill="var(--ring)"/>
      <circle cx="594" cy="663" r="80" fill="var(--sky)"/>
      <!-- gear with orbit -->
      <circle cx="584" cy="663" r="30" fill="none" stroke="var(--white)" stroke-width="14" stroke-dasharray="9 6"/>
      <circle cx="584" cy="663" r="24" fill="none" stroke="var(--white)" stroke-width="6"/>
      <ellipse cx="602" cy="663" rx="34" ry="13" fill="none" stroke="var(--white)" stroke-width="3" transform="rotate(-40 602 663)"/>
      <ellipse cx="602" cy="663" rx="34" ry="13" fill="none" stroke="var(--white)" stroke-width="3" transform="rotate(40 602 663)"/>
      <circle cx="602" cy="663" r="5" fill="var(--white)"/>
    </g>
    <g>
      <circle cx="829" cy="578" r="88" fill="var(--ring)"/>
      <circle cx="829" cy="578" r="80" fill="var(--sky)"/>
      <!-- staff with wings -->
      <rect x="826" y="532" width="6" height="96" rx="3" fill="var(--white)"/>
      <circle cx="829" cy="530" r="7" fill="var(--white)"/>
      <path d="M826,552 q-30,-14 -58,-2 q24,2 30,14 q14,-4 28,-2 z" fill="var(--white)"/>
      <path d="M832,552 q30,-14 58,-2 q-24,2 -30,14 q-14,-4 -28,-2 z" fill="var(--white)"/>
      <path d="M812,570 q34,8 17,20 q-18,12 2,22 q18,8 0,18" fill="none" stroke="var(--white)" stroke-width="4"/>
      <path d="M846,570 q-34,8 -17,20 q18,12 -2,22 q-18,8 0,18" fill="none" stroke="var(--white)" stroke-width="4"/>
    </g>

    <!-- contact tab -->
    <polygon points="552,905 959,905 959,952 532,952" fill="var(--sky-light)"/>
  </svg>

  <div class="brand brand-school"><span class="mark"></span>Birchmont Valley Schools</div>
  <div class="brand brand-college">Westhaven Valley Community College</div>

  <h1 class="title">BRV Early College<br>Program</h1>
  <p class="subtitle">Earn credit for both High School and College and Learn more about the career focused courses in</p>

  <section class="perks">
    <h2>THINGS TO LOOK FORWARD TO:</h2>
    <ul>
      <li><svg viewBox="0 0 14 14"><circle cx="7" cy="7" r="7" fill="var(--sky)"/><path d="M5.5,4 L8.5,7 L5.5,10" fill="none" stroke="#fff" stroke-width="1.8"/></svg>Experience college in high school</li>
      <li><svg viewBox="0 0 14 14"><circle cx="7" cy="7" r="7" fill="var(--sky)"/><path d="M5.5,4 L8.5,7 L5.5,10" fill="none" stroke="#fff" stroke-width="1.8"/></svg>Finish college early</li>
      <li><svg viewBox="0 0 14 14"><circle cx="7" cy="7" r="7" fill="var(--sky)"/><path d="M5.5,4 L8.5,7 L5.5,10" fill="none" stroke="#fff" stroke-width="1.8"/></svg>Save money on college tuition and fees</li>
      <li><svg viewBox="0 0 14 14"><circle cx="7" cy="7" r="7" fill="var(--sky)"/><path d="M5.5,4 L8.5,7 L5.5,10" fill="none" stroke="#fff" stroke-width="1.8"/></svg>Get advice on your future career</li>
    </ul>
  </section>

  <div class="pathway-label" style="left:829px; top:674px;">HEALTH</div>
  <div class="pathway-label" style="left:594px; top:760px;">TECHNOLOGY &amp;<br>ENGINEERING</div>
  <div class="pathway-label" style="left:372px; top:843px;">COMPUTER &amp;<br>INFORMATION SCIENCE</div>
  <div class="pathway-label" style="left:135px; top:899px;">EDUCATION</div>

  <div class="contact-tab"><span>FOR MORE INFORMATION CONTACT</span></div>

  <div class="contact contact-a">
    <h3>Gavin Purdy</h3>
    <p>ZT12 Alliances</p>
    <p>WHVC</p>
    <p class="email"><svg viewBox="0 0 14 10"><rect width="14" height="10" fill="var(--sky-light)"/><path d="M0,0 L7,6 L14,0" fill="none" stroke="var(--navy)" stroke-width="1.2"/></svg>gpurdy@whvc-example.edu</p>
  </div>
  <div class="contact contact-b">
    <h3>Ms. Okafuji</h3>
    <p>Early College Coordinator</p>
    <p>Room J215</p>
    <p class="email"><svg viewBox="0 0 14 10"><rect width="14" height="10" fill="var(--sky-light)"/><path d="M0,0 L7,6 L14,0" fill="none" stroke="var(--navy)" stroke-width="1.2"/></svg>dena.okafuji@birchmont-example.org</p>
  </div>
  <div class="contact contact-c">
    <h3>Ms. Valdivia</h3>
    <p>Work-Based Learning Coordinator</p>
    <p>Room J215</p>
    <p class="email"><svg viewBox="0 0 14 10"><rect width="14" height="10" fill="var(--sky-light)"/><path d="M0,0 L7,6 L14,0" fill="none" stroke="var(--navy)" stroke-width="1.2"/></svg>rosa.valdivia@birchmont-example.org</p>
  </div>
</div>
</body>
</html>
```